Redesign website for small print company

Vindurgata is a small printing company in Iceland mainly servicing Students, schools, etc. We are also doing all kind of other jobs, like business cards, book printing, brochure printing etc. We are also selling books online.
Our website is: www.vindurgata.is
What we are looking for is:
- Web Design (Uncoded - PSD layout only)
- Mobile friendly design, using our current color scheme: Red, green, yellow and light gray.
- Clean simple design
- Simple, light and easy to use.
- More menu Items/drop down
Industry/Entity Type
Digital Printing
Number of Pages Required
5+ page
Requirements
Must have
- Easy navigation
- Designed for mobile
- Current color scheme (see logo)
Nice to have
- Icon based products

```html
<!DOCTYPE html>
<html lang="en">
<head>
<meta charset="utf-8">
<title>Vindurgata – Printing</title>
<link href="https://fonts.googleapis.com/css2?family=Lato:wght@400;700;900&display=swap" rel="stylesheet">
<style>
:root{
  --red:#c0282d;
  --green-dark:#2e5a2a;
  --green:#1f8f55;
  --yellow:#f3c318;
  --gray:#8a8a8a;
  --light:#e6e6e6;
  --ink:#1e1e1e;
  --footer:#1f1d1e;
  --map:#e4e2dd;
  --white:#fff;
}
*{box-sizing:border-box;margin:0;padding:0}
html,body{width:1200px;height:2913px;overflow:hidden;background:var(--white);font-family:'Lato',sans-serif;color:var(--ink)}
.page{position:relative;width:1200px;height:2913px}
.abs{position:absolute}

/* header */
.header{left:0;top:0;width:1200px;height:140px;background:var(--white);z-index:3}
.logo{left:103px;top:0;width:188px;height:198px;background:var(--white);border:1px solid #ddd;box-shadow:0 2px 6px rgba(0,0,0,.15);display:flex;flex-direction:column;align-items:center;justify-content:center;gap:12px;z-index:4}
.logo-square{width:60px;height:60px;background:var(--red)}
.logo-name{font-weight:900;font-size:19px;color:var(--ink);letter-spacing:.5px}
.contact-item{top:20px;display:flex;align-items:center;gap:10px;font-size:19px;color:#333;white-space:nowrap}
.contact-ico{width:36px;height:36px;border-radius:50%;border:2px solid var(--ink);display:flex;align-items:center;justify-content:center}
.nav{top:84px;left:369px;font-size:15px;font-weight:700;color:#333}
.nav a{text-decoration:none;color:inherit;position:absolute;white-space:nowrap}
.nav .active{color:var(--red)}
.signin{left:996px;top:52px;width:105px;height:30px;border:1px solid #bbb;font-size:15px;color:#555;text-align:center;line-height:28px}
.lang{left:936px;top:78px;width:85px;height:27px;border:1px solid #999;font-size:13px;color:var(--green);line-height:25px;padding-left:10px}
.dropdown{left:355px;top:140px;width:529px;height:124px;background:var(--red);z-index:5;color:var(--white);font-size:14px}
.dropdown span{position:absolute;white-space:nowrap}
.dropdown span::before{content:"";display:inline-block;border-left:5px solid var(--white);border-top:4px solid transparent;border-bottom:4px solid transparent;margin-right:10px}
.drop-caret{left:593px;top:130px;border-left:10px solid transparent;border-right:10px solid transparent;border-bottom:10px solid var(--red);z-index:5}

/* hero */
.hero{left:0;top:140px;width:1200px;height:604px;background:linear-gradient(180deg,#6d6d6d 0%,#3e3e3e 55%,#2a2a2a 100%);overflow:hidden}
.hero-title{left:0;top:190px;width:1200px;text-align:center;font-weight:900;font-size:92px;color:var(--white);letter-spacing:1px}
.hero-sub{left:240px;top:290px;width:720px;text-align:center;font-size:15px;font-weight:700;line-height:24px;color:var(--white)}
.hero-arrow{top:258px;width:40px;height:40px;border-radius:50%;background:rgba(255,255,255,.12)}
.hero-curve{left:0;bottom:0}

/* products */
.section-title{left:0;width:1200px;text-align:center;font-weight:900;font-size:34px}
.toolbar{left:101px;width:998px;height:60px;border-top:1px solid var(--light);border-bottom:1px solid var(--light)}
.count{left:126px;top:844px;font-size:14px;color:#666}
.order{left:988px;top:840px;width:86px;height:28px;border:1px solid #ccc;font-size:14px;color:#666;line-height:26px;text-align:center}
.pager{left:1006px;top:898px;font-size:13px;color:#777;display:flex;align-items:center;gap:10px}
.pager i{width:22px;height:22px;border:1px solid #ddd;display:inline-block}
.card{width:229px;height:218px;background:var(--white);border:1px solid;text-align:center}
.card .ico{width:74px;height:74px;border-radius:50%;margin:18px auto 0;display:flex;align-items:center;justify-content:center}
.card h3{font-size:14px;font-weight:900;margin-top:18px;letter-spacing:.3px}
.card p{font-size:12px;line-height:20px;margin:8px 22px 0;color:#333}
.card.featured{background:var(--green-dark);color:var(--white)}
.card.featured p{color:var(--white)}
.bd-red{border-color:#f2cfcf}.bd-yellow{border-color:#f6e6a6}.bd-gray{border-color:#e3e3e3}.bd-green{border-color:#cfe0cf}
.btn{left:470px;top:1451px;width:260px;height:50px;border-radius:25px;background:var(--ink);color:var(--white);font-weight:900;font-size:15px;display:flex;align-items:center;justify-content:center;gap:12px;letter-spacing:.5px}

/* about */
.about{left:0;top:1602px;width:1200px;height:598px;background:var(--green);color:var(--white)}
.about h2{position:absolute;left:0;top:64px;width:1200px;text-align:center;font-size:34px;font-weight:900}
.about h3{position:absolute;left:101px;top:142px;font-size:30px;font-weight:900}
.about .copy{position:absolute;left:101px;top:210px;width:495px;font-size:12.5px;line-height:23px}
.about .copy p{margin-bottom:24px}
.about-frame{left:649px;top:142px;width:436px;height:363px;background:#4aa873;padding:12px}
.about-photo{width:100%;height:100%;background:linear-gradient(160deg,var(--yellow) 0%,var(--yellow) 38%,#d8d2c8 60%,#9c978f 100%)}

/* map */
.map{left:0;top:2200px;width:1200px;height:344px;background:var(--map)}

/* footer */
.footer{left:0;top:2544px;width:1200px;height:369px;background:var(--footer);color:var(--white)}
.footer h4{position:absolute;top:65px;font-size:19px;font-weight:900}
.footer ul{position:absolute;top:103px;list-style:none;font-size:15px}
.footer li{height:29px}
.footer .ci{position:absolute;font-size:15px;line-height:29px;display:flex;gap:14px}
.footer .rule{position:absolute;left:99px;top:285px;width:1002px;height:1px;background:#3a3839}
.footer .legal{position:absolute;left:99px;top:313px;font-size:12px;color:#ccc}
.pay{position:absolute;top:312px;width:44px;height:20px;background:#555;border-radius:3px}
</style>
</head>
<body>
<div class="page">

  <header class="abs header">
    <div class="abs contact-item" style="left:548px">
      <span class="contact-ico" style="border-color:var(--green-dark)"><svg width="16" height="16" viewBox="0 0 24 24"><path fill="#2e5a2a" d="M6.6 10.8a15 15 0 006.6 6.6l2.2-2.2c.3-.3.7-.4 1-.2 1.1.4 2.3.6 3.6.6.6 0 1 .4 1 1V20c0 .6-.4 1-1 1C10.6 21 3 13.4 3 4c0-.6.4-1 1-1h3.5c.6 0 1 .4 1 1 0 1.3.2 2.5.6 3.6.1.3 0 .7-.2 1z"/></svg></span>555 0142
    </div>
    <div class="abs contact-item" style="left:703px">
      <span class="contact-ico" style="border-color:var(--red)"><svg width="16" height="16" viewBox="0 0 24 24"><path fill="#c0282d" d="M2 6h20v12H2z"/><path fill="none" stroke="#fff" stroke-width="2" d="M2 6l10 7 10-7"/></svg></span>verk@vindurgata.is
    </div>
    <div class="abs contact-item" style="left:938px">
      <span class="contact-ico" style="border-color:var(--yellow)"><svg width="16" height="16" viewBox="0 0 24 24"><circle cx="12" cy="12" r="9" fill="none" stroke="#f3c318" stroke-width="2"/><path d="M12 7v5l3 2" fill="none" stroke="#f3c318" stroke-width="2"/></svg></span>Mon - Fri: 9-17
    </div>
    <nav class="abs nav">
      <a class="active" style="left:0">HOME</a>
      <a style="left:81px">ABOUT US</a>
      <a style="left:192px">PRODUCTS</a>
      <a style="left:305px">SERVICES</a>
      <a style="left:408px">CONTACT US</a>
    </nav>
    <div class="abs signin">SIGN IN</div>
    <div class="abs lang">English ⌄</div>
    <svg class="abs" style="left:1043px;top:82px" width="20" height="20" viewBox="0 0 20 20"><circle cx="8" cy="8" r="6" fill="none" stroke="#bbb" stroke-width="2"/><path d="M12.5 12.5L18 18" stroke="#bbb" stroke-width="2"/></svg>
    <svg class="abs" style="left:1080px;top:80px" width="20" height="22" viewBox="0 0 20 22"><rect x="2" y="7" width="16" height="13" fill="none" stroke="#bbb" stroke-width="2"/><path d="M6 7V5a4 4 0 018 0v2" fill="none" stroke="#bbb" stroke-width="2"/></svg>
  </header>

  <div class="abs logo">
    <div class="logo-square"></div>
    <div class="logo-name">VINDURGATA</div>
  </div>

  <div class="abs drop-caret"></div>
  <div class="abs dropdown">
    <span style="left:32px;top:24px">Essays</span>
    <span style="left:32px;top:52px">Business cards</span>
    <span style="left:32px;top:80px">Leaflets</span>
    <span style="left:202px;top:24px">Bookprinting</span>
    <span style="left:202px;top:52px">Posters</span>
    <span style="left:202px;top:80px">Textbooks</span>
    <span style="left:364px;top:24px">Brochure Printing</span>
    <span style="left:364px;top:52px">Calendar 2018</span>
  </div>

  <section class="abs hero" role="img" aria-label="Print shop floor with large printing presses and colour sheets">
    <div class="abs hero-title">VINDURGATA</div>
    <div class="abs hero-sub">Quis autem vel eum iure reprehenderit qui in ea voluptate velit esse quam nihil molestiae consequatur, vel illum qui dolorem eum fugiat quo voluptas nulla.</div>
    <div class="abs hero-arrow" style="left:26px"><svg width="40" height="40"><path d="M23 12l-8 8 8 8" fill="none" stroke="#ddd" stroke-width="2"/></svg></div>
    <div class="abs hero-arrow" style="left:1124px"><svg width="40" height="40"><path d="M17 12l8 8-8 8" fill="none" stroke="#ddd" stroke-width="2"/></svg></div>
    <svg class="abs hero-curve" width="1200" height="60" viewBox="0 0 1200 60" preserveAspectRatio="none"><path d="M0 60 L0 45 Q600 -40 1200 60 Z" fill="#fff"/></svg>
  </section>

  <h2 class="abs section-title" style="top:770px">OUR PRODUCTS</h2>
  <div class="abs toolbar" style="top:825px"></div>
  <div class="abs count">8 Products</div>
  <div class="abs order">Order ⌄</div>
  <div class="abs pager"><i></i>Page<i></i></div>

  <div class="abs card bd-red" style="left:101px;top:932px">
    <div class="ico" style="background:var(--red)"><svg width="34" height="34" viewBox="0 0 34 34"><rect x="6" y="8" width="22" height="18" fill="none" stroke="#fff" stroke-width="2"/><path d="M10 14h14M10 19h14" stroke="#fff" stroke-width="2"/></svg></div>
    <h3>PHOTOCOPYING</h3><p>Lorem ipsum dolor sit amet, consect adipiscing elit, sed do eiusmod tempor incididunt.</p>
  </div>
  <div class="abs card featured" style="left:357px;top:932px;border-color:var(--green-dark)">
    <div class="ico" style="background:var(--white)"><svg width="34" height="34" viewBox="0 0 34 34"><path d="M17 4l5 8v16h-10V12z" fill="none" stroke="#2e5a2a" stroke-width="2"/><path d="M17 14v12" stroke="#2e5a2a" stroke-width="2"/></svg></div>
    <h3>CREATIVE PROCESS</h3><p>Lorem ipsum dolor sit amet, consect adipiscing elit, sed do eiusmod tempor incididunt.</p>
  </div>
  <div class="abs card bd-yellow" style="left:614px;top:932px">
    <div class="ico" style="background:var(--yellow)"><svg width="34" height="34" viewBox="0 0 34 34"><path d="M6 20l14-12 8 8-14 10z" fill="#fff"/><path d="M10 22h16" stroke="#f3c318" stroke-width="2"/></svg></div>
    <h3>SCANNING</h3><p>Lorem ipsum dolor sit amet, consect adipiscing elit, sed do eiusmod tempor incididunt.</p>
  </div>
  <div class="abs card bd-gray" style="left:868px;top:932px">
    <div class="ico" style="background:var(--gray)"><svg width="34" height="34" viewBox="0 0 34 34"><rect x="10" y="5" width="14" height="10" fill="#fff"/><rect x="6" y="14" width="22" height="12" fill="none" stroke="#fff" stroke-width="2"/><rect x="10" y="22" width="14" height="6" fill="#fff"/></svg></div>
    <h3>DIGITAL PRINTING</h3><p>Lorem ipsum dolor sit amet, consect adipiscing elit, sed do eiusmod tempor incididunt.</p>
  </div>

  <div class="abs card bd-gray" style="left:101px;top:1188px">
    <div class="ico" style="background:var(--gray)"><svg width="34" height="34" viewBox="0 0 34 34"><rect x="5" y="9" width="24" height="16" rx="2" fill="none" stroke="#fff" stroke-width="2"/><circle cx="12" cy="16" r="3" fill="#fff"/><path d="M18 15h7M18 19h7" stroke="#fff" stroke-width="2"/></svg></div>
    <h3>BUSINESS CARDS</h3><p>Lorem ipsum dolor sit amet, consect adipiscing elit, sed do eiusmod tempor incididunt.</p>
  </div>
  <div class="abs card bd-yellow" style="left:357px;top:1188px">
    <div class="ico" style="background:var(--yellow)"><svg width="34" height="34" viewBox="0 0 34 34"><path d="M5 9l12 3 12-3v16l-12 3-12-3z" fill="none" stroke="#fff" stroke-width="2"/><path d="M17 12v16" stroke="#fff" stroke-width="2"/></svg></div>
    <h3>TOURIST BROCHURE</h3><p>Lorem ipsum dolor sit amet, consect adipiscing elit, sed do eiusmod tempor incididunt.</p>
  </div>
  <div class="abs card bd-green" style="left:614px;top:1188px">
    <div class="ico" style="background:var(--green-dark)"><svg width="34" height="34" viewBox="0 0 34 34"><path d="M6 12l11-5 11 5-11 5z" fill="#fff"/><path d="M6 17l11 5 11-5M6 22l11 5 11-5" fill="none" stroke="#fff" stroke-width="2"/></svg></div>
    <h3>TEXTBOOKS</h3><p>Lorem ipsum dolor sit amet, consect adipiscing elit, sed do eiusmod tempor incididunt.</p>
  </div>
  <div class="abs card bd-red" style="left:868px;top:1188px">
    <div class="ico" style="background:var(--red)"><svg width="34" height="34" viewBox="0 0 34 34"><rect x="8" y="5" width="18" height="24" fill="none" stroke="#fff" stroke-width="2"/><path d="M12 23v-5M16 23v-9M20 23v-7" stroke="#fff" stroke-width="2"/></svg></div>
    <h3>REPORTS</h3><p>Lorem ipsum dolor sit amet, consect adipiscing elit, sed do eiusmod tempor incididunt.</p>
  </div>

  <div class="abs btn">VIEW ALL PRODUCTS <svg width="16" height="16" viewBox="0 0 16 16"><circle cx="8" cy="8" r="8" fill="#fff"/><path d="M5 8h6M8 5l3 3-3 3" fill="none" stroke="#1e1e1e" stroke-width="2"/></svg></div>

  <section class="abs about">
    <h2>ABOUT US</h2>
    <h3>Welcome to University</h3>
    <div class="copy">
      <p>University education is a company located in the campus, which has specialized in the service of school staff, as well as providing general public printing.</p>
      <p>Higher education publishes seminars and first-class textbooks for courses, prints theses for lesson, as well as working on an unprecedented number of smaller pieces for students, teachers and organizations. These include brochures, reports, questionnaires, business cards, books, OCR scanning and more.</p>
      <p>Higher education is a tailored print shop. The Heron is the official eco-label of the Nordic countries, which has created a foothold in this country and is known among consumers.</p>
      <p>University education is located at the corner of Birkigata and Hlíðargata. (walked into Hlíðargötumegin)</p>
    </div>
    <div class="abs about-frame"><div class="about-photo" role="img" aria-label="Hand with pen marking colour swatches on a yellow background"></div></div>
  </section>

  <div class="abs map" role="img" aria-label="Street map showing where the shop is located"></div>

  <footer class="abs footer">
    <h4 style="left:99px">COMPANY</h4>
    <ul style="left:99px"><li>Home</li><li>About Us</li><li>Products</li><li>Services</li><li>Contact Us</li></ul>
    <ul style="left:330px"><li>Terms of Use</li><li>Privacy Policy</li><li>Site Map</li></ul>
    <h4 style="left:614px">SOCIAL MEDIA</h4>
    <ul style="left:614px"><li>Newsfeed</li><li>Microblog</li><li>Worknet</li></ul>
    <h4 style="left:911px">CONTACT US</h4>
    <div class="ci" style="left:911px;top:103px"><svg width="16" height="22" viewBox="0 0 16 22" style="margin-top:4px"><path d="M8 0a8 8 0 018 8c0 6-8 14-8 14S0 14 0 8a8 8 0 018-8z" fill="#fff"/><circle cx="8" cy="8" r="3" fill="#1f1d1e"/></svg><span>vindurgata.is,<br>Reykjavik 101</span></div>
    <div class="ci" style="left:911px;top:190px"><svg width="16" height="16" viewBox="0 0 24 24" style="margin-top:6px"><path fill="#fff" d="M6.6 10.8a15 15 0 006.6 6.6l2.2-2.2c.3-.3.7-.4 1-.2 1.1.4 2.3.6 3.6.6.6 0 1 .4 1 1V20c0 .6-.4 1-1 1C10.6 21 3 13.4 3 4c0-.6.4-1 1-1h3.5c.6 0 1 .4 1 1 0 1.3.2 2.5.6 3.6.1.3 0 .7-.2 1z"/></svg><span>555 0142</span></div>
    <div class="ci" style="left:911px;top:219px"><svg width="18" height="14" viewBox="0 0 18 14" style="margin-top:8px"><rect width="18" height="14" fill="#fff"/><path d="M0 0l9 7 9-7" fill="none" stroke="#1f1d1e" stroke-width="1.5"/></svg><span>verk@vindurgata.is</span></div>
    <div class="rule"></div>
    <div class="legal">© 2018 VINDURGATA. All right reserved Term of Use</div>
    <div class="pay" style="left:1020px"></div>
    <div class="pay" style="left:1070px;width:30px"></div>
  </footer>

</div>
</body>
</html>
```